The Brookhaven Sessions - Concert Series Website Design

I've recently decided to launch a concert series in my living room and would love a website to use to promote the series. I'm looking for a simple Wix design that I could take over once it's complete. I'll provide the logo for which I'd like the website to utilize the color scheme.

Target Market(s)

Music lovers in Denver

Industry/Entity Type

Music

Coding

Coded - Design and coding required

Number of Pages Required

2 page

Font styles to use
Script

Requirements
Must have
• 2 pages - one for concert goers to see the schedule and rsvp, and one for artists about the booking process

```html
<!DOCTYPE html>
<html lang="en">
<head>
<meta charset="utf-8">
<title>The Brookhaven Sessions</title>
<link href="https://fonts.googleapis.com/css2?family=Marcellus&family=Roboto:wght@400;500;700&display=swap" rel="stylesheet">
<style>
:root{
  --maroon:#7a2340;
  --orange:#e8894f;
  --btn-end:#7c2d36;
  --cream:#fbf0e6;
  --ink:#2a2a2a;
  --muted:#555;
  --footer:#1e0a0e;
  --white:#fff;
  --line:#777;
}
*{margin:0;padding:0;box-sizing:border-box}
html,body{width:1200px;height:4258px;overflow:hidden}
body{position:relative;font-family:'Roboto',sans-serif;color:var(--ink);background:var(--white)}
.abs{position:absolute}
.display{font-family:'Marcellus',serif;font-weight:400}
.btn{position:absolute;height:60px;border-radius:30px;background:linear-gradient(90deg,var(--orange),var(--btn-end));color:var(--white);font:700 17px 'Roboto',sans-serif;display:flex;align-items:center;justify-content:center;letter-spacing:.2px}

/* hero */
.hero{left:0;top:0;width:1200px;height:856px;background:radial-gradient(ellipse at 60% 35%,#7a5232 0%,#4a2e1e 45%,#1c1218 100%)}
.hero-shade{left:0;top:0;width:1200px;height:856px;background:linear-gradient(180deg,rgba(20,12,18,.1),rgba(24,16,30,.55))}
.brand{left:145px;top:22px;display:flex;align-items:center;gap:14px}
.brand-mark{width:88px;height:88px;border-radius:50%;background:var(--maroon)}
.brand-name{font-family:'Marcellus',serif;color:var(--white);font-size:34px;line-height:30px}
.brand-name small{display:block;font-size:18px;line-height:18px}
.nav{top:54px;font:500 17px 'Roboto',sans-serif;color:var(--white)}
.nav-active{border-bottom:2px solid var(--white);padding-bottom:4px}
.login{left:936px;top:40px;width:119px;height:49px;gap:10px}
.hero-title{left:144px;top:312px;color:var(--white);font-size:50px;line-height:68px;letter-spacing:1px}
.hero-sub{left:144px;top:535px;color:var(--white);font:700 21px 'Roboto',sans-serif}

/* about */
.about{left:0;top:856px;width:1200px;height:764px;background:var(--white)}
.mountain-fade{left:0;width:729px;height:200px;background:linear-gradient(180deg,rgba(255,255,255,0),#c9c9c9)}
.about-photo{left:729px;top:845px;width:471px;height:745px;background:linear-gradient(160deg,#b58a5a,#5b3b2a 55%,#2e2420)}
.section-title{color:var(--maroon);font-size:60px;line-height:74px}
.body-text{font-size:18px;line-height:34px;color:var(--muted);text-align:justify}

/* shows */
.shows{left:0;top:1620px;width:1200px;height:1091px;background:var(--cream)}
.card{position:absolute;top:1860px;width:359px;text-align:center}
.card-photo{width:359px;height:446px}
.card-date{margin-top:34px;color:var(--orange);font-size:17px}
.card-name{margin-top:16px;font:700 20px 'Roboto',sans-serif;color:var(--ink)}
.card-text{margin-top:14px;font-size:17px;line-height:24px;color:var(--muted)}

/* contact */
.contact{left:0;top:2711px;width:1200px;height:573px;background:var(--white)}
.field{position:absolute;width:407px;border-bottom:1.5px solid var(--line);font-size:17px;color:var(--ink);padding-bottom:18px;display:flex;justify-content:space-between}
.caret{width:0;height:0;border-left:5px solid transparent;border-right:5px solid transparent;border-top:6px solid var(--ink);margin-top:6px;margin-right:8px}
.band-photo{left:0;top:3284px;width:1200px;height:589px;background:linear-gradient(120deg,#3a2a26,#8a5a3c 45%,#b67a4e 60%,#3a2a2a)}

/* footer */
.footer{left:0;top:3873px;width:1200px;height:385px;background:var(--footer);color:var(--white)}
.foot-title{color:var(--orange);font:700 22px 'Roboto',sans-serif}
.foot-item{font-size:17px;color:var(--white)}
.social{top:4180px;width:28px;height:28px;border-radius:50%;border:2px solid var(--white)}
</style>
</head>
<body>

<section class="abs hero" role="img" aria-label="Photo of friends playing acoustic guitar in a warm living room"></section>
<div class="abs hero-shade"></div>

<header>
  <div class="abs brand">
    <div class="brand-mark"></div>
    <div class="brand-name"><small>THE</small>BROOKHAVEN<br>SESSIONS</div>
  </div>
  <nav>
    <span class="abs nav nav-active" style="left:729px">HOME</span>
    <span class="abs nav" style="left:821px">ARTISTS</span>
    <a class="btn login">
      <svg width="16" height="16" viewBox="0 0 16 16"><circle cx="8" cy="4.5" r="3.5" fill="#fff"/><path d="M1 16c0-4 3-6 7-6s7 2 7 6z" fill="#fff"/></svg>LOGIN
    </a>
  </nav>
</header>

<h1 class="abs display hero-title">LIVE MUSIC.<br>SHARED SPACE.<br>GOLDEN-HOUR ENERGY.</h1>
<p class="abs hero-sub">An intimate living-room concert series in Denver.</p>
<a class="btn" style="left:144px;top:602px;width:185px">GET STARTED</a>

<section class="abs about"></section>
<div class="abs mountain-fade" style="top:1420px" role="img" aria-label="Faint snowy mountain range"></div>
<div class="abs about-photo" role="img" aria-label="Photo of a singer performing in a home studio"></div>
<h2 class="abs display section-title" style="left:144px;top:922px">ABOUT<br>THE SERIES</h2>
<p class="abs body-text" style="left:144px;top:1097px;width:511px">The Brookhaven Sessions is a small, invitation-style concert series hosted in a Denver living room—created to bring artists and listeners closer, one performance at a time.</p>
<p class="abs body-text" style="left:144px;top:1231px;width:511px">Sed ut perspiciatis unde omnis iste natus error sit voluptatem accusantium doloremque laudantium, totam rem aperiam, eaque ipsa quae ab illo inventore veritatis et quasi architecto beatae vitae dicta sunt explicabo. Nemo enim ipsam voluptatem quia voluptas sit aspernatur aut odit aut fugit</p>
<a class="btn" style="left:144px;top:1438px;width:186px">READ MORE</a>

<section class="abs shows"></section>
<h2 class="abs display section-title" style="left:0;width:1200px;text-align:center;top:1722px">UPCOMING SHOWS</h2>
<article class="card" style="left:36px">
  <div class="card-photo" role="img" aria-label="Photo of a singer with a microphone and drummer behind" style="background:linear-gradient(150deg,#6d5a4e,#a57a66 50%,#3b3434)"></div>
  <div class="card-date">March 03,2026</div>
  <div class="card-name">MAREN HOLLOWAY</div>
  <div class="card-text">Sed ut perspiciatis unde omnis<br>iste natus erroloptat</div>
</article>
<article class="card" style="left:420px">
  <div class="card-photo" role="img" aria-label="Photo of a guitarist singing with a friend cheering" style="background:linear-gradient(150deg,#8a7a66,#5a4a3a 55%,#2f2a28)"></div>
  <div class="card-date">March 03,2026</div>
  <div class="card-name">THE RIDGELINE ECHOES</div>
  <div class="card-text">Sed ut perspiciatis unde omnis<br>iste natus erroloptat</div>
</article>
<article class="card" style="left:803px">
  <div class="card-photo" role="img" aria-label="Photo of a drummer in a sunlit loft" style="background:linear-gradient(150deg,#caa176,#7a5a3e 55%,#2e2220)"></div>
  <div class="card-date">March 03,2026</div>
  <div class="card-name">SINGER-SONGWRITER</div>
  <div class="card-text">Sed ut perspiciatis unde omnis<br>iste natus erroloptat</div>
</article>
<a class="btn" style="left:507px;top:2532px;width:184px">VIEW MORE</a>

<section class="abs contact"></section>
<div class="abs" style="left:0;top:3110px;width:1200px;height:174px;background:linear-gradient(180deg,rgba(255,255,255,0),#bdbdbd)" role="img" aria-label="Faint snowy mountain range"></div>
<h2 class="abs display section-title" style="left:144px;top:2829px">CONTACT US</h2>
<p class="abs body-text" style="left:578px;top:2836px;width:477px">Sed ut perspiciatis unde omnis iste natus error sit voluptatem accusantium doloremque laudantium,</p>
<div class="field" style="left:144px;top:2985px">Enter Name</div>
<div class="field" style="left:600px;top:2985px">Enter Email</div>
<div class="field" style="left:144px;top:3070px">Number of guests<span class="caret"></span></div>
<div class="field" style="left:600px;top:3070px">Select Show<span class="caret"></span></div>
<a class="btn" style="left:507px;top:3166px;width:184px">SUBMIT</a>

<div class="abs band-photo" role="img" aria-label="Photo of a band with keyboard, singer and guitarists performing"></div>

<footer class="abs footer"></footer>
<div class="abs brand" style="top:3951px">
  <div class="brand-mark"></div>
  <div class="brand-name"><small>THE</small>BROOKHAVEN<br>SESSIONS</div>
</div>
<h3 class="abs foot-title" style="left:583px;top:3944px">CONTACT</h3>
<svg class="abs" style="left:584px;top:4006px" width="18" height="16" viewBox="0 0 18 16"><path d="M1 3l5-2 6 2 5-2v12l-5 2-6-2-5 2z" fill="#e8894f"/></svg>
<p class="abs foot-item" style="left:617px;top:4004px;line-height:27px">123,Loremi psum dolor sit<br>vluptuminuummsi</p>
<svg class="abs" style="left:584px;top:4070px" width="17" height="17" viewBox="0 0 24 24"><path d="M6.6 10.8a15 15 0 006.6 6.6l2.2-2.2a1 1 0 011-.25 11 11 0 003.6.6 1 1 0 011 1V20a1 1 0 01-1 1A17 17 0 013 4a1 1 0 011-1h3.5a1 1 0 011 1 11 11 0 00.6 3.6 1 1 0 01-.25 1z" fill="#e8894f"/></svg>
<p class="abs foot-item" style="left:622px;top:4067px">+1 303 555 0147</p>
<svg class="abs" style="left:584px;top:4099px" width="18" height="14" viewBox="0 0 18 14"><rect width="18" height="14" rx="1" fill="#e8894f"/><path d="M1 1l8 6 8-6" stroke="#1e0a0e" stroke-width="1.5" fill="none"/></svg>
<p class="abs foot-item" style="left:622px;top:4095px">hello@brookhavensessions.com</p>
<h3 class="abs foot-title" style="left:965px;top:3944px">LINKS</h3>
<p class="abs foot-item" style="left:965px;top:4004px">Home</p>
<p class="abs foot-item" style="left:965px;top:4039px">Artists</p>
<span class="abs social" style="left:145px"></span>
<span class="abs social" style="left:183px"></span>
<span class="abs social" style="left:221px"></span>
<span class="abs social" style="left:259px"></span>
<p class="abs foot-item" style="left:479px;top:4184px">© 2026 Brookhaven Sessions.All Rights Reserved &nbsp;|&nbsp; Privacy Policy &nbsp;|&nbsp; Terms of use</p>

</body>
</html>
```